Fitness Equipment & Service

I want to make the card eye catching and fun. We are called Corvane Motion Limited and we are based in Wales. We sell, install and service all types of fitness equipment from Skipping ropes, right through the Dumbbells, Kettle bells and Barbells through to state of the art Treadmills, Running Machines and Strength Equipment. We also design and install changing room furniture and lockers.

TYPOGRAPHY
We would like to use Futrura. Futura has an appearance of efficiency and forwardness. The typeface is derived
from simple geometric forms (near-perfect circles, triangles and squares) and is based on strokes of
near-even weight, which are low in contrast. This is most visible in the almost perfectly round stroke of
the o, which is nonetheless slightly ovoid.
The lowercase has tall ascenders, which rise above the cap line. The uppercase
characters present proportions similar to those of classical Roman capitals.

TYPOGRAPHIC CONSIDERATIONS
No Strike though
No Horizontal Scaling
No Drop Shadows
No Effects
Never use less than 120% Leading

OUR CORPORATE COLOURS
BRAND GUIDELINES
We were thinking that our primary colour palette consists of the Acid Green (Pantone 382) and Process Black.

We work closely with tquarly Ltd and would like to include their name on the card somewhere. I have attached images of the other brands that we work with as an idea or the small icons I have included that illustrate what we do?. I have very kindly been given permission to use any of the images off the files that I have included below, so I hope these help. I will include these below. I would be open to suggestions if it made the card more striking Can you do it?
Updates

Hi All, Just wanted to add a few thoughts but you are the guys with the creative visions (thats why are here) We are based in Wales, UK and we would be open to lots of different ideas on a theme but must be eye catching, Bold and FUN. If you can or think that the Welsh or any dragon could be put in there then go for it (its not a must have) We have also added some ideas for colour but again its over to you!! GO FOR IT ! Thanks and look forward to your visions! Owen

Hi All, Just thought I would sen through the contact details that need to be on the card. (if you want to play around with icons instead of the wording twitter, Facebook, go for it): Corvane Motion Limited Owen Pritchard Managing Director Mob: +44 (0)7582 913 406 e-mail: sales@corvanemotion.co.uk Web: Corvanemotion.co.uk twitter: @motionLetterbin Facebook: Corvane Motion Limited

```html
<!DOCTYPE html>
<html lang="en">
<head>
<meta charset="utf-8">
<title>Corvane Motion Limited – Business Card</title>
<link href="https://fonts.googleapis.com/css2?family=Jost:wght@400;500&display=swap" rel="stylesheet">
<style>
  :root {
    --backdrop: #939393;
    --card: #f3f3f5;
    --black: #161616;
    --acid-green: #c4d600;
    --acid-green-text: #9aab00;
    --ink: #333333;
  }
  html, body {
    margin: 0;
    width: 1105px;
    height: 1200px;
    overflow: hidden;
    background: var(--backdrop);
    font-family: "Jost", "Futura", sans-serif;
  }
  .card {
    position: absolute;
    left: 182px;
    width: 747px;
    height: 427px;
    background: var(--card);
    overflow: hidden;
  }
  .card--front { top: 119px; }
  .card--back { top: 636px; }

  .edge-tab {
    position: absolute;
    left: -16px;
    top: 222px;
    width: 30px;
    height: 62px;
    border-radius: 50%;
    background: var(--black);
  }
  .brand-mark {
    position: absolute;
    border-radius: 50%;
    background: radial-gradient(circle at 45% 40%, var(--acid-green) 0%, #5e6a00 45%, var(--black) 85%);
  }
  .card--front .brand-mark { left: 536px; top: 28px; width: 170px; height: 170px; }
  .card--front .brand-name {
    position: absolute;
    left: 501px; top: 206px; width: 240px;
    text-align: center;
    font-size: 15px; font-weight: 500; line-height: 1.2;
    color: var(--black);
  }
  .holder-name {
    position: absolute; left: 43px; top: 224px; margin: 0;
    font-size: 29px; font-weight: 500; line-height: 1.2;
    color: var(--black);
  }
  .holder-role {
    position: absolute; left: 43px; top: 258px; margin: 0;
    font-size: 21px; font-weight: 400; line-height: 1.2;
    color: var(--acid-green-text);
  }
  .rule {
    position: absolute; left: 43px; top: 295px;
    width: 670px; height: 2px;
    background: var(--acid-green);
  }
  .social {
    position: absolute; left: 659px; top: 264px;
    display: flex; gap: 6px;
  }
  .social span {
    width: 23px; height: 23px;
    background: var(--black);
  }
  .contact {
    position: absolute; left: 43px; top: 312px;
    margin: 0; padding: 0; list-style: none;
  }
  .contact li {
    display: flex; align-items: center;
    height: 29px;
    font-size: 20px; line-height: 1.2;
    color: var(--ink);
  }
  .contact svg { width: 18px; height: 18px; margin-right: 10px; fill: var(--black); }
  .partner {
    position: absolute; right: 34px; top: 341px;
    margin: 0; text-align: right;
    font-size: 20px; line-height: 29px;
    color: var(--ink);
  }

  .card--back .brand-mark { left: 280px; top: 61px; width: 186px; height: 186px; }
  .card--back .brand-name {
    position: absolute; left: 0; right: 0; top: 292px;
    text-align: center;
    font-size: 30px; font-weight: 500; line-height: 1.2;
    letter-spacing: 1px;
    color: var(--black);
  }
</style>
</head>
<body>

<section class="card card--front">
  <div class="edge-tab"></div>
  <div class="brand-mark" role="img" aria-label="Corvane Motion Limited brand mark"></div>
  <div class="brand-name">Corvane Motion Limited</div>

  <h1 class="holder-name">Owen Pritchard</h1>
  <p class="holder-role">Managing Director</p>
  <div class="social" aria-label="Social profiles"><span></span><span></span></div>
  <div class="rule"></div>

  <ul class="contact">
    <li>
      <svg viewBox="0 0 18 18" aria-hidden="true"><path d="M5 1h8a1 1 0 0 1 1 1v14a1 1 0 0 1-1 1H5a1 1 0 0 1-1-1V2a1 1 0 0 1 1-1zm1 2v10h6V3zm3 11a1 1 0 1 0 0 2 1 1 0 0 0 0-2z"/></svg>
      +44 (0)7582 913 406
    </li>
    <li>
      <svg viewBox="0 0 18 18" aria-hidden="true"><path d="M2 4h14v10H2zm1 1.2v.4l6 4 6-4v-.4zm0 1.6V13h12V6.8l-6 4z"/></svg>
      sales@corvanemotion.co.uk
    </li>
    <li>
      <svg viewBox="0 0 18 18" aria-hidden="true"><circle cx="9" cy="9" r="7.5"/><path d="M4 6c2 0 3 1 3 3s2 2 2 4M11 3c0 2 2 2 3 3" stroke="#f3f3f5" stroke-width="1.4" fill="none"/></svg>
      www.Corvanemotion.co.uk
    </li>
  </ul>

  <p class="partner">Working with tquarly Ltd<br>Wales, UK</p>
</section>

<section class="card card--back">
  <div class="brand-mark" role="img" aria-label="Corvane Motion Limited brand mark"></div>
  <div class="brand-name">CORVANE MOTION LIMITED</div>
</section>

</body>
</html>
```